Chimney Service company needs new business card design

We need a updated business card with our new logo added. We provide a full range of chimney services throughout Vermont and New Hampshire. The business card will be one sided and color. Attached is our current business card another document showing all the information we would like on the card.
We dont like a lot of flashy colors.... here is a link to our website to get an idea of our branding www.flueguardianvt.example

Target Market(s)

homeowners

Industry/Entity Type

Business

Contact Information for Business Card

See attached sheet for content.

Font styles to use
Serif
Sans Serif

Requirements
Must have
• all information provided on separate sheet
Should not have
• Additional information that may clogg up design

```html
<!DOCTYPE html>
<html lang="en">
<head>
<meta charset="utf-8">
<title>Flue Guardian – Business Card</title>
<link rel="stylesheet" href="https://fonts.googleapis.com/css2?family=Cinzel:wght@400;500&family=Didact+Gothic&display=swap">
<style>
  :root {
    --page: #e9e6e1;
    --card-white: #f7f7f5;
    --charcoal: #2f3031;
    --charcoal-light: #444546;
    --brand-red: #a61c22;
    --ink: #3a3a3a;
    --on-dark: #e8e8e8;
    --serif: "Cinzel", "Times New Roman", serif;
    --sans: "Didact Gothic", "Helvetica Neue", Arial, sans-serif;
  }
  * { box-sizing: border-box; margin: 0; padding: 0; }
  html, body { width: 1200px; height: 1022px; overflow: hidden; }
  body { background: var(--page); position: relative; }

  .business-card {
    position: absolute; left: 75px; top: 211px;
    width: 1050px; height: 600px;
    background: var(--card-white);
    box-shadow: 0 12px 40px rgba(0,0,0,.18);
    overflow: hidden;
  }

  /* Left brand column */
  .brand-column {
    position: absolute; left: 0; top: 345px; width: 288px; height: 255px;
    display: flex; flex-direction: column; align-items: center; justify-content: center;
    gap: 16px;
  }
  .brand-mark { width: 26px; height: 26px; background: var(--charcoal); }
  .brand-name {
    font-family: var(--serif); font-weight: 400; font-size: 26px;
    color: var(--charcoal); letter-spacing: 2px; text-align: center; line-height: 1.25;
  }

  /* Header: company name */
  .company-header {
    position: absolute; right: 50px; top: 40px; width: 460px; text-align: center;
  }
  .company-name {
    font-family: var(--serif); font-weight: 400; font-size: 46px; color: var(--ink);
    letter-spacing: 3px; line-height: 1;
  }
  .company-est {
    display: flex; align-items: center; gap: 14px; margin-top: 8px;
    font-family: var(--serif); font-weight: 400; font-size: 19px; color: var(--ink); letter-spacing: 3px;
  }
  .company-est::before, .company-est::after {
    content: ""; flex: 1; height: 3px; background: var(--charcoal);
  }

  /* Contact panel */
  .contact-panel {
    position: absolute; right: 50px; top: 140px; width: 380px; height: 170px;
    background: var(--brand-red); color: #fff;
    display: flex; flex-direction: column; justify-content: center; gap: 8px;
    padding-left: 26px; font-family: var(--sans); font-style: normal; font-size: 22px;
  }
  .contact-line { display: flex; align-items: center; gap: 12px; white-space: nowrap; }
  .contact-line svg { width: 18px; height: 18px; flex: none; }

  /* Services band */
  .services-band {
    position: absolute; left: 300px; top: 345px; right: 0; bottom: 0;
    background: linear-gradient(180deg, var(--charcoal-light), var(--charcoal));
    padding: 36px 0 0 34px;
  }
  .divider-horizontal {
    position: absolute; left: 300px; right: 0; top: 335px; height: 2px;
    background: var(--brand-red);
  }
  .divider-vertical {
    position: absolute; left: 288px; top: 345px; bottom: 0; width: 2px;
    background: var(--brand-red);
  }
  .services-list {
    list-style: none; font-family: var(--sans); font-size: 25px; color: var(--on-dark);
    letter-spacing: 1.5px; line-height: 1.5; text-transform: uppercase;
  }
  .services-list li::before { content: "●"; font-size: 14px; margin-right: 14px; vertical-align: 3px; }
  .services-list .inline-dot { font-size: 18px; margin: 0 6px; vertical-align: 2px; }
</style>
</head>
<body>
  <article class="business-card">
    <div class="brand-column">
      <span class="brand-mark"></span>
      <span class="brand-name">Flue<br>Guardian</span>
    </div>

    <header class="company-header">
      <h1 class="company-name">FLUE GUARDIAN</h1>
      <p class="company-est">INC 1994</p>
    </header>

    <address class="contact-panel">
      <span class="contact-line">
        <svg viewBox="0 0 20 20" fill="#fff"><path d="M5 2l3 4-2 2c1 2 3 4 5 5l2-2 4 3-2 3C9 17 3 11 3 4z"/></svg>
        802-555-0147
      </span>
      <span class="contact-line">
        <svg viewBox="0 0 20 20" fill="none" stroke="#fff" stroke-width="2"><rect x="2" y="4" width="16" height="12"/><path d="M2 4l8 7 8-7"/></svg>
        info@flueguardianvt.example
      </span>
      <span class="contact-line">
        <svg viewBox="0 0 20 20" fill="none" stroke="#fff" stroke-width="1.6"><circle cx="10" cy="10" r="8"/><path d="M2 10h16M10 2c-4 4-4 12 0 16M10 2c4 4 4 12 0 16"/></svg>
        www.flueguardianvt.example
      </span>
    </address>

    <span class="divider-horizontal"></span>
    <span class="divider-vertical"></span>
    <section class="services-band">
      <ul class="services-list">
        <li>Full Masonry Services</li>
        <li>Historic Chimney Restoration</li>
        <li>Stainless Steel Liners</li>
        <li>HSCB Certified Chimney Sweep</li>
        <li>Fully Insured <span class="inline-dot">●</span> Free Estimates</li>
      </ul>
    </section>
  </article>
</body>
</html>
```